Velvet Lantern rebranding my business with a new business card

I have my new logo and now I need a refresher on my business cards. I really want something fun and fresh. I like black background or anything to make the color pop.
Logo
Name: Velvet Lantern
Contact Info as stated below:
Mira Pellow
555-013-4762
Logo
Name: Velvet Lantern
Mira Pellow
555-013-4762
fb.me/VelvetLanternbyMira
Instagram: @VelvetLanternbyMira

Industry/Entity Type

Business

Contact Information for Business Card

double-sided. Logo on one side. Contact info on the other.

Requirements
Must have
• Logo
• Name: Velvet Lantern
• Contact Info as stated below:
• Mira Pellow
• 555-013-4762
• fb.me/VelvetLanternbyMira
• fb.me/VelvetLanternbyMira

```html
<!DOCTYPE html>
<html lang="en">
<head>
<meta charset="utf-8">
<title>Velvet Lantern – Business Card</title>
<link rel="stylesheet" href="https://fonts.googleapis.com/css2?family=Delius&family=Ubuntu:wght@400;500&display=swap">
<style>
  :root {
    --backdrop: #ececec;
    --teal: #5cc5ae;
    --teal-deep: #4fb8a1;
    --pink: #f4c6ce;
    --pink-ring: #e9a9b6;
    --paper: #ffffff;
    --ink: #232323;
    --brand: #c95f86;
  }
  * { box-sizing: border-box; margin: 0; padding: 0; }
  html, body {
    width: 1200px;
    height: 576px;
    overflow: hidden;
    background: var(--backdrop);
  }
  .sheet {
    position: relative;
    width: 1200px;
    height: 576px;
  }
  .card {
    position: absolute;
    top: 138px;
    width: 484px;
    height: 293px;
    border-radius: 14px;
    overflow: hidden;
  }

  /* Front: logo side */
  .card--front {
    left: 82px;
    background: var(--teal);
  }
  .card--front .pattern-area {
    position: absolute;
    inset: 0;
    background: linear-gradient(160deg, var(--teal) 0%, var(--teal-deep) 100%);
  }
  .emblem {
    position: absolute;
    left: 138px;
    top: 43px;
    width: 208px;
    height: 208px;
    border-radius: 50%;
    background: var(--paper);
    border: 2px solid #2b2b2b;
    box-shadow: inset 0 0 0 5px var(--paper), inset 0 0 0 7px var(--pink-ring);
    display: flex;
    align-items: center;
    justify-content: center;
  }
  .brand-name {
    font-family: "Ubuntu", sans-serif;
    font-weight: 500;
    color: var(--brand);
    text-align: center;
    line-height: 1.1;
  }
  .emblem .brand-name { font-size: 26px; }

  /* Back: contact side */
  .card--back {
    left: 602px;
    background: var(--paper);
  }
  .card--back .wave {
    position: absolute;
    inset: 0;
    width: 100%;
    height: 100%;
  }
  .card--back .brand-mark {
    position: absolute;
    left: 42px;
    top: 70px;
    width: 180px;
    height: 90px;
    display: flex;
    align-items: center;
    justify-content: center;
  }
  .card--back .brand-name { font-size: 26px; }
  .holder {
    position: absolute;
    right: 26px;
    top: 24px;
    text-align: right;
  }
  .holder__name {
    font-family: "Delius", cursive;
    font-size: 29px;
    letter-spacing: 1px;
    color: var(--ink);
  }
  .holder__title {
    font-family: "Ubuntu", sans-serif;
    font-size: 11px;
    color: var(--ink);
    margin-top: 2px;
  }
  .contacts {
    position: absolute;
    right: 26px;
    top: 218px;
    list-style: none;
    font-family: "Ubuntu", sans-serif;
    font-size: 16px;
    color: var(--ink);
  }
  .contacts li {
    display: flex;
    align-items: center;
    justify-content: flex-end;
    gap: 8px;
    height: 26px;
  }
  .contact-icon {
    width: 18px;
    height: 18px;
    flex: none;
  }
</style>
</head>
<body>
<main class="sheet">

  <section class="card card--front" aria-label="Card front">
    <div class="pattern-area" role="img" aria-label="Teal polka dot pattern background"></div>
    <div class="emblem">
      <p class="brand-name">Velvet<br>Lantern</p>
    </div>
  </section>

  <section class="card card--back" aria-label="Card back">
    <svg class="wave" viewBox="0 0 484 293" preserveAspectRatio="none" aria-hidden="true">
      <path d="M0,210 C150,245 300,205 484,132 L484,148 C300,222 150,258 0,232 Z" fill="var(--pink)" opacity="0.8"/>
      <path d="M0,240 C160,262 300,236 484,168 L484,175 C300,244 160,270 0,250 Z" fill="var(--pink)" opacity="0.55"/>
      <path d="M0,262 C150,278 300,252 484,158 L484,293 L0,293 Z" fill="var(--teal)"/>
    </svg>

    <div class="brand-mark">
      <p class="brand-name">Velvet Lantern</p>
    </div>

    <header class="holder">
      <h1 class="holder__name">Mira Pellow</h1>
      <p class="holder__title">Managing Director</p>
    </header>

    <ul class="contacts">
      <li>
        <span>555-013-4762</span>
        <svg class="contact-icon" viewBox="0 0 18 18" aria-label="Phone">
          <rect x="1" y="1" width="16" height="16" rx="3.5" fill="none" stroke="var(--ink)" stroke-width="1.5"/>
          <path d="M6 4.5 L7.6 6.5 L6.8 7.7 C7.4 9 8.6 10.3 10 11 L11.3 10.2 L13.3 11.8 L12.4 13.4 C9 13.2 5 9.4 4.7 5.6 Z" fill="var(--ink)"/>
        </svg>
      </li>
      <li>
        <span>VelvetLanternbyMira</span>
        <svg class="contact-icon" viewBox="0 0 18 18" aria-hidden="true">
          <rect x="1" y="1" width="16" height="16" rx="3.5" fill="none" stroke="var(--ink)" stroke-width="1.5"/>
        </svg>
      </li>
    </ul>
  </section>

</main>
</body>
</html>
```